Profesional personal website needs design and business card

I need a business card with my professional name as a logo "Dorian Vitality" for my business. I am a Wellness Coach, consultant and trainer. So it should be professional, wellness oriented and modern.

Target Market(s)

Private clients, governments, corporations. Luxury and high market.

Industry/Entity Type

Health And Wellness

Contact Information for Business Card

Dorian Vitality should be the logo

Colors

Designer to choose colors to be used in the design.

Requirements
Must have
• Dorian Vitality
• Name: Tomás Lirandel
• Wellness Coach, Consultant & Trainer.
• Website: www.dorianvitality-example.com
• Phone:
• Spain (+34) 612 480 317
• (USA) +1 (555) 610 4829
Nice to have
• The most important is the design of "Dorian Vitality", as this is going to be my personal brand logo. It should be professional, wellness, high end and actual.
Should not have
• no golds, no baroque style..

```html
<!DOCTYPE html>
<html lang="en">
<head>
<meta charset="utf-8">
<title>Dorian Vitality – Business Card</title>
<link rel="stylesheet" href="https://fonts.googleapis.com/css2?family=Arimo:wght@400;700&family=Roboto+Condensed:wght@400&display=swap">
<style>
  :root {
    --backdrop: #e4e6e8;
    --card: #fbfbfa;
    --teal: #4e9e99;
    --grey: #6d6e71;
    --ink: #5f6062;
  }
  html, body {
    margin: 0;
    padding: 0;
    width: 1200px;
    height: 936px;
    overflow: hidden;
    background: var(--backdrop);
  }
  .business-card {
    position: absolute;
    left: 100px;
    top: 163px;
    width: 1000px;
    height: 610px;
    background: var(--card);
    box-shadow: 0 10px 30px rgba(0,0,0,0.12);
  }
  .brand {
    position: absolute;
    left: 196px;
    top: 282px;
    display: flex;
    align-items: center;
    gap: 12px;
  }
  .brand-dot {
    width: 20px;
    height: 20px;
    border-radius: 50%;
    background: var(--teal);
    flex: none;
  }
  .brand-name {
    font-family: "Arimo", Arial, sans-serif;
    font-weight: 700;
    font-size: 20px;
    line-height: 1.15;
    letter-spacing: 2px;
    color: var(--grey);
    text-transform: uppercase;
  }
  .details {
    position: absolute;
    left: 409px;
    top: 206px;
  }
  .person-name {
    margin: 0;
    font-family: "Arimo", Arial, sans-serif;
    font-weight: 700;
    font-size: 37px;
    line-height: 1;
    color: var(--teal);
    text-transform: uppercase;
  }
  .person-role {
    margin: 6px 0 0;
    font-family: "Roboto Condensed", "Arial Narrow", sans-serif;
    font-size: 23px;
    color: var(--grey);
  }
  .contact-list {
    list-style: none;
    margin: 22px 0 0;
    padding: 0;
  }
  .contact-item {
    display: flex;
    align-items: center;
    gap: 12px;
    height: 38px;
    font-family: "Arimo", Arial, sans-serif;
    font-size: 25px;
    color: var(--ink);
  }
  .contact-icon {
    width: 24px;
    height: 24px;
    flex: none;
  }
</style>
</head>
<body>
  <div class="business-card">
    <div class="brand">
      <div class="brand-dot"></div>
      <div class="brand-name">Dorian<br>Vitality</div>
    </div>

    <div class="details">
      <h1 class="person-name">Tomás Lirandel</h1>
      <p class="person-role">Wellness Coach, Consultant &amp; Trainer</p>
      <ul class="contact-list">
        <li class="contact-item">
          <svg class="contact-icon" viewBox="0 0 24 24" aria-hidden="true">
            <circle cx="12" cy="12" r="10.5" fill="none" stroke="var(--teal)" stroke-width="1.6"/>
            <path d="M9 7.2l1.4 2.3-1 1.2c.7 1.5 1.8 2.6 3.3 3.3l1.2-1 2.3 1.4-.6 1.8c-3.8-.2-7.1-3.5-7.3-7.3z" fill="var(--teal)"/>
          </svg>
          <span>+34 612 480 317</span>
        </li>
        <li class="contact-item">
          <svg class="contact-icon" viewBox="0 0 24 24" aria-hidden="true">
            <circle cx="12" cy="12" r="10.5" fill="none" stroke="var(--teal)" stroke-width="1.6"/>
            <path d="M9 7.2l1.4 2.3-1 1.2c.7 1.5 1.8 2.6 3.3 3.3l1.2-1 2.3 1.4-.6 1.8c-3.8-.2-7.1-3.5-7.3-7.3z" fill="var(--teal)"/>
          </svg>
          <span>+1 (555) 610 4829</span>
        </li>
        <li class="contact-item">
          <svg class="contact-icon" viewBox="0 0 24 24" aria-hidden="true">
            <g fill="none" stroke="var(--teal)" stroke-width="1.6">
              <circle cx="12" cy="12" r="10"/>
              <ellipse cx="12" cy="12" rx="4.5" ry="10"/>
              <line x1="2" y1="12" x2="22" y2="12"/>
              <line x1="4" y1="7" x2="20" y2="7"/>
              <line x1="4" y1="17" x2="20" y2="17"/>
            </g>
          </svg>
          <span>www.dorianvitality-example.com</span>
        </li>
      </ul>
    </div>
  </div>
</body>
</html>
```